BildeVOLD buisnesscard

Hey :) I need a modern buisnesscard for my company BildeVOLD
It most have:
Dagligleder og Fotograf: Henrik Audun Strandvik

Mob: +4791264085
Epost: post@bildevold.example
Adresse: Kvernbakken9, 6040 Fjordvik

Facbook and instagram logo with text BildeVOLD

BildeVOLD logo

It Company

```html
<!DOCTYPE html>
<html lang="no">
<head>
<meta charset="utf-8">
<title>BildeVOLD – visittkort</title>
<link rel="stylesheet" href="https://fonts.googleapis.com/css2?family=Titillium+Web:ital,wght@0,400;0,600;1,700&display=swap">
<style>
  :root {
    --backdrop: #4a3f3a;
    --card: #1b1b1c;
    --card-edge: #2a2a2b;
    --ink: #b9b9b9;
    --ink-soft: #9a9a9a;
    --mark: #3a3a3b;
  }
  * { box-sizing: border-box; margin: 0; padding: 0; }
  html, body { width: 1200px; height: 716px; overflow: hidden; }
  body {
    background: var(--backdrop);
    font-family: "Titillium Web", Arial, sans-serif;
    position: relative;
  }
  .card {
    position: absolute;
    top: 208px;
    width: 520px;
    height: 300px;
    background: var(--card);
    border: 1px solid var(--card-edge);
    border-radius: 4px;
    box-shadow: 0 14px 30px rgba(0,0,0,.45);
  }
  .card--front { left: 50px; }
  .card--back { left: 630px; }

  .front-brand {
    position: absolute;
    inset: 0;
    display: flex;
    align-items: center;
    justify-content: center;
    font-size: 44px;
    font-weight: 600;
    color: var(--mark);
    letter-spacing: .5px;
  }

  .identity { position: absolute; left: 42px; top: 92px; }
  .identity__name {
    font-size: 19px;
    font-weight: 700;
    font-style: italic;
    color: var(--ink);
    line-height: 1.1;
  }
  .identity__role { font-size: 13px; color: var(--ink-soft); margin-top: 2px; }

  .contact { position: absolute; left: 42px; top: 150px; list-style: none; }
  .contact__item {
    display: flex;
    align-items: center;
    gap: 9px;
    font-size: 13px;
    color: var(--ink-soft);
    line-height: 21px;
  }
  .contact__icon { width: 11px; height: 11px; fill: var(--ink-soft); flex: none; }

  .brand { position: absolute; right: 40px; top: 104px; text-align: center; }
  .brand__name { font-size: 34px; font-weight: 600; color: var(--ink); line-height: 1; }
  .brand__web { font-size: 13px; color: var(--ink-soft); margin-top: 8px; }

  .social {
    position: absolute;
    right: 40px;
    bottom: 26px;
    display: flex;
    align-items: center;
    gap: 7px;
    font-size: 14px;
    color: var(--ink-soft);
  }
  .social__square { width: 12px; height: 12px; background: var(--ink-soft); border-radius: 2px; }
</style>
</head>
<body>
  <section class="card card--front">
    <div class="front-brand">BildeVOLD</div>
  </section>

  <section class="card card--back">
    <div class="identity">
      <p class="identity__name">Henrik Audun Strandvik</p>
      <p class="identity__role">Managing Director &amp; Photographer</p>
    </div>

    <ul class="contact">
      <li class="contact__item">
        <svg class="contact__icon" viewBox="0 0 12 12" aria-hidden="true"><rect x="3" y="0" width="6" height="12" rx="1"/><rect x="4" y="1.5" width="4" height="7" fill="#1b1b1c"/></svg>
        +4791264085
      </li>
      <li class="contact__item">
        <svg class="contact__icon" viewBox="0 0 12 12" aria-hidden="true"><rect x="0" y="2" width="12" height="8" rx="1"/><path d="M0.5 2.5 6 7 11.5 2.5" fill="none" stroke="#1b1b1c" stroke-width="1.2"/></svg>
        post@bildevold.example
      </li>
      <li class="contact__item">
        <svg class="contact__icon" viewBox="0 0 12 12" aria-hidden="true"><path d="M6 0a4 4 0 0 0-4 4c0 3 4 8 4 8s4-5 4-8a4 4 0 0 0-4-4z"/><circle cx="6" cy="4" r="1.5" fill="#1b1b1c"/></svg>
        Kvernbakken9, 6040 Fjordvik
      </li>
    </ul>

    <div class="brand">
      <p class="brand__name">BildeVOLD</p>
      <p class="brand__web">www.bildevold.example</p>
    </div>

    <div class="social">
      <span class="social__square"></span>
      <span>/BildeVOLD</span>
    </div>
  </section>
</body>
</html>
```